Push notification screens at app start up

We have an existing news publication app platform and are adding categories to push notifications.

We need two screens designed (each for Zorbel, Quillet and Android for a total of 6d) that show when the app is first launched.

The workflow of our app:
0. app launch screen while webservices run (no work needed)
1. information screen to the user promoting the benefits of push notification with "Next" button. (see concept attached)
2. Push categories selection screen. This will have list of category types, with on/off switch.

"Select the categories that you wish to receive occasional notices:
Breaking News (on/off switch)
Local News (on/off switch)
Sports (on/off switch)
Local Events (on/off switch)
Weather Alerts (on/off switch)
Local Deals (on/off switch)"

"Enable these categories on the next screen."
"Next" button

Background:
When I was looking around at app designs, I came across this one (http://www.plinthworks.example/design/7719034) and I really liked it. We obviously have different features on our screen, but I’d like to have this same feel. The colors used in this design are perfect.

UPDATE: I do not mean to limit your design to match the layout as the one mentioned above. Please use your creativity for the layout.

Our standard font in Helvetica Neue.

Notes:
- our app is developed for all phone devices from Zorbel 4 to Zorbel 6, so designs should be thoughtful of vertical scrolling if needed.
- our app is developed for Quillets, so we'll need designs completed as well. (We can finalize Zorbel design first, then translate the design to Quillet.)
- our app is developed for Android phones (not tablets), so we'll need designs completed as well. (We can finalize iOS design first, then translater to Android UI design guidelines).

We hope to establish a good on-going relationship with the designer for as-needed work in the future.

News

• Helvetica Neue

• Clean designs. No clutter.
• We would likely go with the standard on/off switches for both iOS and Android, but are open to small custom variations.

```html
<!DOCTYPE html>
<html lang="en">
<head>
<meta charset="utf-8">
<title>Notifications onboarding screen</title>
<link rel="stylesheet" href="https://fonts.googleapis.com/css2?family=Arimo:wght@400;700&display=swap">
<style>
  :root {
    --bg: #ffffff;
    --brand-blue: #2470f4;
    --card-bg: #ebebeb;
    --card-border: #cfcfcf;
    --text-dark: #333333;
    --text-body: #3a3a3a;
    --status-text: #222222;
    --white: #ffffff;
  }
  * { margin: 0; padding: 0; box-sizing: border-box; }
  html, body {
    width: 675px;
    height: 1200px;
    overflow: hidden;
    background: var(--bg);
    font-family: "Arimo", "Helvetica Neue", Helvetica, Arial, sans-serif;
  }
  .screen {
    position: relative;
    width: 675px;
    height: 1200px;
    background: var(--bg);
  }
  .status-bar {
    position: absolute;
    top: 0; left: 0; right: 0;
    height: 46px;
    display: flex;
    align-items: center;
    padding: 0 14px;
    font-size: 17px;
    color: var(--status-text);
  }
  .status-left { display: flex; align-items: center; gap: 8px; flex: 1; }
  .signal-dots { display: flex; gap: 3px; }
  .signal-dots span {
    width: 11px; height: 11px; border-radius: 50%;
    border: 1.5px solid var(--status-text);
  }
  .signal-dots span.on { background: var(--status-text); }
  .status-time {
    position: absolute; left: 0; right: 0; text-align: center;
    font-weight: 700; pointer-events: none;
  }
  .status-right { display: flex; align-items: center; gap: 8px; }
  .battery {
    width: 44px; height: 20px; border: 2px solid var(--status-text);
    border-radius: 4px; padding: 2px; position: relative;
  }
  .battery::after {
    content: ""; position: absolute; right: -6px; top: 5px;
    width: 3px; height: 7px; background: var(--status-text); border-radius: 0 2px 2px 0;
  }
  .battery-level { width: 100%; height: 100%; background: var(--status-text); border-radius: 1px; }

  .hero-icon {
    position: absolute;
    left: 234px; top: 113px;
    width: 207px; height: 207px;
    border-radius: 50%;
    background: var(--brand-blue);
    display: flex; align-items: center; justify-content: center;
  }

  .info-card {
    position: absolute;
    left: 27px; top: 410px;
    width: 621px; height: 546px;
    background: var(--card-bg);
    border: 2px solid var(--card-border);
    border-radius: 18px;
    text-align: center;
  }
  .info-title {
    margin-top: 60px;
    font-size: 41px;
    font-weight: 700;
    color: var(--text-dark);
  }
  .info-text {
    margin-top: 38px;
    font-size: 20px;
    line-height: 29px;
    color: var(--text-body);
  }
  .info-text + .info-text { margin-top: 29px; }
  .next-button {
    position: absolute;
    left: 18px; right: 18px; bottom: 25px;
    height: 97px;
    border: none;
    border-radius: 11px;
    background: var(--brand-blue);
    color: var(--white);
    font-family: inherit;
    font-size: 33px;
    font-weight: 700;
    letter-spacing: 0.5px;
  }
</style>
</head>
<body>
<main class="screen">
  <header class="status-bar">
    <div class="status-left">
      <div class="signal-dots"><span class="on"></span><span class="on"></span><span class="on"></span><span></span><span></span></div>
      <span class="carrier">VOLT</span>
      <svg class="wifi" width="22" height="16" viewBox="0 0 22 16" aria-hidden="true">
        <path d="M11 15 L7.5 11 A5 5 0 0 1 14.5 11 Z" fill="#222"/>
        <path d="M4.5 8 A9 9 0 0 1 17.5 8" fill="none" stroke="#222" stroke-width="2.2"/>
        <path d="M1.5 4.8 A13.5 13.5 0 0 1 20.5 4.8" fill="none" stroke="#222" stroke-width="2.2"/>
      </svg>
    </div>
    <span class="status-time">4:21 PM</span>
    <div class="status-right">
      <span class="battery-percent">100%</span>
      <div class="battery"><div class="battery-level"></div></div>
    </div>
  </header>

  <div class="hero-icon">
    <svg width="120" height="100" viewBox="0 0 120 100" aria-hidden="true" fill="none" stroke="#fff" stroke-width="5" stroke-linejoin="round" stroke-linecap="round">
      <path d="M14 38 L30 38 L66 16 L66 84 L30 62 L14 62 Z"/>
      <path d="M30 38 L30 62"/>
      <path d="M24 62 L32 88 L44 88 L38 66"/>
      <path d="M80 40 A14 14 0 0 1 80 60"/>
      <path d="M90 30 A26 26 0 0 1 90 70"/>
      <path d="M100 20 A38 38 0 0 1 100 80"/>
    </svg>
  </div>

  <section class="info-card">
    <h1 class="info-title">Notifications</h1>
    <p class="info-text">By enabling push notifications, you can keep up to<br>date with occasional notifications related to items you<br>care about. Select the categories on the next screen<br>and then authorize the push notifications.</p>
    <p class="info-text">If you ever change your mind, you can adjust these<br>options in the Settings menu of this app.</p>
    <button class="next-button" type="button">NEXT</button>
  </section>
</main>
</body>
</html>
```